Bramblewood Card Company Business Cards

We are a trading card store with Glimmorax, sports and other TCG cards, we need a business card design that encompasses a clean cut, modern style with a retro flare. website is bramblewoodcardco.com for reference. Can utilize a comic book era feel or a more modern outdoor feel to utilize the "Pacific Northwest" elements of tress, mountains, etc.

Industry/Entity Type

Trading cards and collectibles

Contact Information for Business Card

business name, email address, phone number, name, owner job title

Font styles to use
Sans Serif

```html
<!DOCTYPE html>
<html lang="en">
<head>
<meta charset="utf-8">
<title>Bramblewood Card Company – Business Card</title>
<link rel="stylesheet" href="https://fonts.googleapis.com/css2?family=Open+Sans:wght@400;600;700;800&display=swap">
<style>
  :root {
    --stage: #d6d6d6;
    --paper: #ffffff;
    --sky: #22bddf;
    --sand: #c9b27f;
    --plum: #6e1f3b;
    --ink: #2f2f2f;
    --slate: #6f6f6f;
  }
  html, body {
    margin: 0;
    width: 1200px;
    height: 1018px;
    overflow: hidden;
    background: var(--stage);
    font-family: "Open Sans", sans-serif;
  }
  .sheet {
    position: relative;
    width: 1200px;
    height: 1018px;
  }
  .card {
    position: absolute;
    left: 250px;
    width: 700px;
    height: 400px;
    overflow: hidden;
    box-shadow: 0 10px 30px rgba(0,0,0,0.18);
  }
  .card-front { top: 79px; background: var(--paper); }
  .card-back  { top: 539px; background: var(--sky); }

  .front-wave {
    position: absolute;
    inset: 0;
    width: 700px;
    height: 400px;
  }
  .holder {
    position: absolute;
    left: 96px;
    top: 52px;
  }
  .holder-name {
    margin: 0;
    font-size: 34px;
    font-weight: 800;
    letter-spacing: 0.5px;
    color: var(--plum);
    line-height: 1;
  }
  .holder-role {
    margin: 4px 0 0;
    font-size: 15px;
    color: var(--ink);
  }
  .contacts {
    position: absolute;
    left: 62px;
    top: 140px;
    margin: 0;
    padding: 0;
    list-style: none;
    font-size: 15px;
    color: var(--ink);
    line-height: 19px;
  }
  .contact-row {
    display: flex;
    align-items: flex-start;
    gap: 14px;
    margin-bottom: 6px;
  }
  .contact-icon {
    flex: none;
    width: 22px;
    height: 22px;
    margin-top: 4px;
  }
  .accent-lines {
    position: absolute;
    left: 358px;
    top: 176px;
    width: 40px;
    height: 150px;
  }
  .brand-mark {
    position: absolute;
    display: flex;
    align-items: center;
    gap: 12px;
    font-weight: 800;
    font-size: 22px;
    line-height: 1.15;
    text-transform: uppercase;
    letter-spacing: 1px;
  }
  .card-front .brand-mark {
    left: 440px;
    top: 180px;
    width: 230px;
    color: var(--slate);
  }
  .card-back .brand-mark {
    left: 225px;
    top: 160px;
    width: 260px;
    color: var(--paper);
  }
  .brand-dot {
    flex: none;
    width: 18px;
    height: 18px;
    border-radius: 50%;
    background: var(--sky);
  }
  .card-back .brand-dot { background: var(--paper); }
</style>
</head>
<body>
<main class="sheet">

  <section class="card card-front" aria-label="Business card front">
    <svg class="front-wave" viewBox="0 0 700 400" aria-hidden="true">
      <path d="M0 300 C 40 330, 70 372, 160 400 L 0 400 Z" fill="var(--sky)"/>
      <path d="M0 290 C 80 350, 300 330, 560 370 C 610 378, 650 390, 680 400 L 0 400 Z" fill="var(--sky)"/>
      <path d="M0 262 C 60 340, 300 330, 560 372" fill="none" stroke="var(--sand)" stroke-width="8"/>
      <path d="M0 248 C 60 330, 300 322, 560 366" fill="none" stroke="var(--paper)" stroke-width="4"/>
    </svg>

    <header class="holder">
      <h1 class="holder-name">DALEN WHITCOMBE</h1>
      <p class="holder-role">Founder</p>
    </header>

    <ul class="contacts">
      <li class="contact-row">
        <svg class="contact-icon" viewBox="0 0 22 22" aria-hidden="true">
          <circle cx="11" cy="11" r="11" fill="var(--sky)"/>
          <rect x="7.5" y="5" width="7" height="12" rx="1.5" fill="none" stroke="#fff" stroke-width="1.4"/>
        </svg>
        <span>+1 360 555 0142<br>+1 360 555 0187</span>
      </li>
      <li class="contact-row">
        <svg class="contact-icon" viewBox="0 0 22 22" aria-hidden="true">
          <circle cx="11" cy="11" r="11" fill="var(--sky)"/>
          <circle cx="11" cy="11" r="5.5" fill="none" stroke="#fff" stroke-width="1.4"/>
          <path d="M5.5 11h11M11 5.5c-2.5 3-2.5 8 0 11M11 5.5c2.5 3 2.5 8 0 11" fill="none" stroke="#fff" stroke-width="1"/>
        </svg>
        <span>info@bramblewoodcardco.com<br>www.bramblewoodcardco.com</span>
      </li>
      <li class="contact-row">
        <svg class="contact-icon" viewBox="0 0 22 22" aria-hidden="true">
          <circle cx="11" cy="11" r="11" fill="var(--sky)"/>
          <path d="M11 17c-3-3.5-4.5-5.8-4.5-7.8a4.5 4.5 0 0 1 9 0c0 2-1.5 4.3-4.5 7.8z" fill="#fff"/>
          <circle cx="11" cy="9.3" r="1.6" fill="var(--sky)"/>
        </svg>
        <span>2214 Cedar Ridge Lane 40<br>Alder Falls, WA 98402</span>
      </li>
    </ul>

    <svg class="accent-lines" viewBox="0 0 40 150" aria-hidden="true">
      <line x1="4" y1="0" x2="4" y2="150" stroke="var(--sky)" stroke-width="2"/>
      <line x1="20" y1="22" x2="20" y2="128" stroke="var(--sky)" stroke-width="2"/>
      <line x1="36" y1="40" x2="36" y2="112" stroke="var(--sky)" stroke-width="2"/>
    </svg>

    <div class="brand-mark">
      <span class="brand-dot" aria-hidden="true"></span>
      <span>Bramblewood Card Company</span>
    </div>
  </section>

  <section class="card card-back" aria-label="Business card back">
    <div class="brand-mark">
      <span class="brand-dot" aria-hidden="true"></span>
      <span>Bramblewood Card Company</span>
    </div>
  </section>

</main>
</body>
</html>
```